Professional Photography Business cards

I need business cards that include my logo which I have uploaded. I run a photography business. I am open to ideas but I would like one side to have my logo and the other side to have my contact info. I don't have a website made but I do own a website domain. I have uploaded 2 different logo color schemes. My business colors are Blue, black , and white.

Business Name
Business Phone Number
Business Email
Business Website address
Instagram

Industry/Entity Type

Professional Photography

Contact Information for Business Card

Phone Number: 916-384-7702 email: info@tlane-studio.example Instagram: @t.lanestudio website doman- www.tlane-studio.example

Requirements
Must have
• I like the idea of a business card with a full black background front and back of card. My colors must include royal blue, black, and white

```html
<!DOCTYPE html>
<html lang="en">
<head>
<meta charset="utf-8">
<title>T. Lane Studio – Business Cards</title>
<link href="https://fonts.googleapis.com/css2?family=Arimo:wght@400&display=swap" rel="stylesheet">
<style>
  :root {
    --backdrop: #b4b4b4;
    --royal-blue: #000ca0;
    --ink-black: #000000;
    --paper-white: #ffffff;
    --text-dark: #1a1a1a;
    --rule-grey: #8a8a8a;
  }
  * { margin: 0; padding: 0; box-sizing: border-box; }
  html, body {
    width: 1200px; height: 1200px; overflow: hidden;
    background: var(--backdrop);
    font-family: "Arimo", Arial, sans-serif;
  }
  .stage { position: relative; width: 1200px; height: 1200px; }
  .card {
    position: absolute; top: 305px; width: 371px; height: 598px;
    overflow: hidden;
    box-shadow: 3px 4px 6px rgba(0,0,0,0.45);
  }
  .card-front { left: 202px; background: var(--royal-blue); }
  .card-back { left: 603px; background: var(--paper-white); }

  .front-top-band {
    position: absolute; left: 0; top: 0; width: 100%; height: 223px;
    background: var(--ink-black);
  }
  .front-mark {
    position: absolute; left: 145px; top: 240px; width: 160px; height: 160px;
  }
  .front-brand {
    position: absolute; left: 90px; width: 270px; top: 418px;
    text-align: center; color: var(--paper-white);
    font-size: 28px; letter-spacing: 0.5px;
  }
  .front-url {
    position: absolute; left: 0; right: 0; top: 531px;
    text-align: center; color: var(--paper-white); font-size: 16.5px;
  }

  .back-brand {
    position: absolute; left: 0; right: 0; top: 140px;
    text-align: center; color: var(--royal-blue);
    font-size: 34px; letter-spacing: 1px;
  }
  .contact-icons {
    position: absolute; left: 0; top: 385px; width: 100%; height: 28px;
  }
  .contact-lines {
    position: absolute; left: 0; right: 0; top: 422px;
    text-align: center; color: var(--text-dark);
    font-size: 17px; line-height: 21.5px;
  }
  .social-row {
    position: absolute; left: 0; top: 497px; width: 100%; height: 28px;
  }
  .social-handle {
    position: absolute; left: 0; right: 0; top: 531px;
    text-align: center; color: var(--text-dark); font-size: 17px;
  }
</style>
</head>
<body>
<main class="stage">
  <section class="card card-front">
    <div class="front-top-band"></div>
    <svg class="front-mark" viewBox="0 0 160 160" aria-hidden="true">
      <circle cx="80" cy="80" r="74" fill="none" stroke="var(--ink-black)" stroke-width="11"/>
    </svg>
    <p class="front-brand">T. Lane Studio</p>
    <p class="front-url">www.tlane-studio.example</p>
  </section>

  <section class="card card-back">
    <p class="back-brand">T. Lane Studio</p>

    <svg class="contact-icons" viewBox="0 0 371 28" aria-hidden="true">
      <line x1="98" y1="14" x2="141" y2="14" stroke="var(--rule-grey)" stroke-width="1"/>
      <line x1="233" y1="14" x2="269" y2="14" stroke="var(--rule-grey)" stroke-width="1"/>
      <rect x="143" y="1" width="25" height="25" rx="3" fill="var(--royal-blue)"/>
      <path d="M148 11 q7.5 -6 15 0 v2 h-4 v-2 h-7 v2 h-4z" fill="var(--paper-white)"/>
      <rect x="151" y="14" width="9" height="7" rx="1" fill="var(--paper-white)"/>
      <rect x="172" y="1" width="25" height="25" rx="3" fill="var(--royal-blue)"/>
      <rect x="177" y="8" width="15" height="11" fill="none" stroke="var(--paper-white)" stroke-width="1.5"/>
      <path d="M177 8 l7.5 6 l7.5 -6" fill="none" stroke="var(--paper-white)" stroke-width="1.5"/>
      <rect x="201" y="1" width="25" height="25" rx="3" fill="var(--royal-blue)"/>
      <circle cx="213.5" cy="13.5" r="7.5" fill="var(--paper-white)"/>
      <path d="M210 9 q3 1 2 4 q-2 1 -1 4 M215 8 q2 3 4 3" fill="none" stroke="var(--royal-blue)" stroke-width="1.4"/>
    </svg>

    <div class="contact-lines">
      <p>916-384-7702</p>
      <p>info@tlane-studio.example</p>
      <p>www.tlane-studio.example</p>
    </div>

    <svg class="social-row" viewBox="0 0 371 28" aria-hidden="true">
      <line x1="98" y1="14" x2="165" y2="14" stroke="var(--rule-grey)" stroke-width="1"/>
      <line x1="202" y1="14" x2="269" y2="14" stroke="var(--rule-grey)" stroke-width="1"/>
      <circle cx="183.5" cy="14" r="13" fill="var(--royal-blue)"/>
    </svg>
    <p class="social-handle">@t.lanestudio</p>
  </section>
</main>
</body>
</html>
```